Company selling food supplements with CBD needs label.

We need a label design for a company called "VEKA Works ltd", is based in the UK, the market name is "NOLVI" or "NOLVI Natural Oils Lovingly Valued". The initial product is Virgin Organic Hemp Seed Oil with a CBD in a 10ml amber dropper bottle. The design should be simplicity and luxury. The design should include also box.

Target Market(s)

Food supplements on Tradeshelf UK

Industry/Entity Type

Supplement

Font styles to use
Other font styles liked:
• Some luxury

Colors

Designer to choose colors to be used in the design.

Requirements
Must have
• All the information on the label required by the UK for the food supplements, the same on the box. One version matt one transparent. The design should include different CBD content, one different bottle (250mg, 500mg, 750mg, 1000mg) .
• The label and box should include the following phrases: "DIRECTIONS: Food Supplement. Shake well before use. Use 4-6 drops 2-3 times a day. Leave the oil in your mouth for 30-60 seconds before swallowing. Gradually build up the dose to find your optimum dosage.
• CAUTION: Do not exceed the recommended daily intake. Do not use as a substitute for a varied diet. Do not use during pregnancy and breastfeeding. Store in a dark and cool place, away from sunlight. Keep away from children.
• INGREDIENTS: Hemp Seed Oil, Omega-6 (2800mg), Omega-3 (930mg), CBD (250mg)
• MANUFACTURED: VEKA Works Ltd, 87 Pelbury Rd, Harrow, HA7 2QX, www,vekaworks.example, info@vekaworks.example.
• EXPIRED DATE: "
• The box should also include a place for bark code.
Nice to have
• Simple and elegant design vertical or horizontal with exposed company logo "NOLVI" or "NOLVI Natural Oils Lovingly Valued". The company logo is provided but designers may change it freely.
Should not have
• The best without pictures/graphics overloading simplicity and purity of design.

```html
<!DOCTYPE html>
<html lang="en">
<head>
<meta charset="UTF-8">
<title>NOLVI CBD Oil Label</title>
<link href="https://fonts.googleapis.com/css2?family=Montserrat:wght@300;400;500;700&display=swap" rel="stylesheet">
<style>
  :root {
    --page-bg: #ffffff;
    --label-black: #2a2725;
    --label-gold: #b19a55;
    --gold-text: #a98d3f;
    --label-white: #ffffff;
    --rule-gold: #9c8440;
  }
  * { margin: 0; padding: 0; box-sizing: border-box; }
  html, body {
    width: 1200px;
    height: 900px;
    overflow: hidden;
    background: var(--page-bg);
    font-family: "Montserrat", sans-serif;
  }
  .canvas {
    width: 1200px;
    height: 900px;
    display: flex;
    justify-content: center;
    align-items: center;
    gap: 60px;
  }
  .label {
    width: 240px;
    height: 340px;
    background: var(--label-black);
    color: var(--label-white);
    display: flex;
    flex-direction: column;
    align-items: center;
    padding-top: 50px;
  }
  .brand-band {
    width: 100%;
    height: 100px;
    background: var(--label-gold);
    display: flex;
    flex-direction: column;
    align-items: center;
    justify-content: center;
  }
  .brand-name {
    font-size: 52px;
    font-weight: 500;
    letter-spacing: 1px;
    line-height: 1;
    color: var(--label-white);
  }
  .brand-tagline {
    font-size: 8px;
    font-weight: 400;
    letter-spacing: 0.3px;
    margin-top: 10px;
    color: var(--label-white);
  }
  .product-name {
    margin-top: 22px;
    font-size: 17px;
    font-weight: 300;
    line-height: 1.3;
    text-align: center;
  }
  .divider {
    width: 165px;
    height: 1.5px;
    background: var(--rule-gold);
    margin-top: 12px;
  }
  .strength {
    margin-top: 10px;
    font-size: 30px;
    font-weight: 300;
    line-height: 1.1;
  }
  .product-type {
    font-size: 27px;
    font-weight: 700;
    color: var(--gold-text);
    letter-spacing: 1px;
    line-height: 1.2;
  }
  .net-weight {
    margin-top: 10px;
    font-size: 12px;
    font-weight: 300;
  }
</style>
</head>
<body>
  <main class="canvas">
    <section class="label">
      <div class="brand-band">
        <span class="brand-name">NOLVI</span>
        <span class="brand-tagline">NATURAL OILS LOVINGLY VALUED</span>
      </div>
      <p class="product-name">VIRGIN ORGANIC<br>HEMP SEED OIL</p>
      <div class="divider"></div>
      <p class="strength">1000mg</p>
      <p class="product-type">CBD OIL</p>
      <p class="net-weight">Net Wt 10ml (.34 fl oz)</p>
    </section>
    <section class="label">
      <div class="brand-band">
        <span class="brand-name">NOLVI</span>
        <span class="brand-tagline">NATURAL OILS LOVINGLY VALUED</span>
      </div>
      <p class="product-name">VIRGIN ORGANIC<br>HEMP SEED OIL</p>
      <div class="divider"></div>
      <p class="strength">1000mg</p>
      <p class="product-type">CBD OIL</p>
      <p class="net-weight">Net Wt 10ml (.34 fl oz)</p>
    </section>
  </main>
</body>
</html>
```